Frostbell Fairgrounds LV, A Magical Holiday Festival

frostbellfairgroundslv.example
Need to include the following:
Dates: Dec 14- Dec 30
kids 48'' and under free, presale tickets $6, wonder pass $25(17 days pass) website: frostbellfairgroundslv.example, ice skating rink, snow park, santa house, first 1000 kids will receive a gift from Santa on Christmas day.
Location: Brackenmoor Casino, 4717 Copperfield Lane.
Also need to include QRM logo and Grand Harvest Supper Fair logo (I attached)

Industry/Entity Type

Festival

Font styles to use
Decorative

Requirements
Must have
• Date : December 14- December 30
• Location: Brackenmoor Casino
Nice to have
• Santa House, christmas lights, ice skating rink, snow park

```html
<!DOCTYPE html>
<html lang="en">
<head>
<meta charset="utf-8">
<title>Frostbell Fairgrounds LV – A Magical Holiday Festival</title>
<link href="https://fonts.googleapis.com/css2?family=Cinzel:wght@400;600&family=Playfair+Display:wght@900&family=Roboto+Condensed:wght@400;700&family=Roboto:wght@400;500&display=swap" rel="stylesheet">
<style>
  :root {
    --page-bg: #cfe0f7;
    --flyer-black: #050505;
    --white: #ffffff;
    --gold: #e6c27a;
    --gold-light: #fff3d2;
    --location-gold: #e0a93a;
    --link-blue: #4f7fd6;
    --partner-red: #d8322e;
    --partner-navy: #1f3f8f;
  }
  html, body {
    margin: 0;
    width: 1200px;
    height: 1200px;
    overflow: hidden;
    background: var(--page-bg);
  }
  .flyer {
    position: absolute;
    left: 149px;
    top: 21px;
    width: 902px;
    height: 1158px;
    background: var(--flyer-black);
    overflow: hidden;
    box-shadow: 6px 8px 14px rgba(0,0,0,0.35);
  }
  .hero-scene {
    position: absolute;
    left: 0; top: 42px;
    width: 902px; height: 680px;
    background:
      radial-gradient(circle at 76% 40%, rgba(70,110,220,0.55) 0 18%, transparent 34%),
      radial-gradient(ellipse at 20% 35%, rgba(140,130,60,0.75), transparent 60%),
      radial-gradient(ellipse at 45% 70%, rgba(160,60,50,0.55), transparent 55%),
      linear-gradient(180deg, #1a1a12 0%, #3b3a1c 40%, #2a1f1a 75%, var(--flyer-black) 100%);
  }
  .hero-shade {
    position: absolute; inset: 0;
    background: linear-gradient(90deg, rgba(0,0,0,0.1), rgba(0,0,0,0.35) 50%, rgba(0,0,0,0.1));
  }
  .brand-mark {
    position: absolute;
    top: 88px; left: 0; width: 100%;
    text-align: center;
    font-family: "Cinzel", serif;
    font-weight: 600;
    color: var(--gold);
    font-size: 40px;
    line-height: 46px;
  }
  .event-title {
    position: absolute;
    top: 252px; left: 0; width: 100%;
    text-align: center;
    font-family: "Cinzel", serif;
    font-weight: 400;
    color: var(--white);
    margin: 0;
  }
  .event-title .name { display: block; font-size: 58px; line-height: 72px; }
  .event-title .tagline { display: block; font-size: 44px; line-height: 58px; }
  .event-dates {
    position: absolute;
    top: 446px; left: 0; width: 100%;
    text-align: center;
    font-family: "Playfair Display", serif;
    font-weight: 900;
    font-size: 76px;
    line-height: 90px;
    color: var(--gold);
    background: linear-gradient(180deg, var(--gold-light) 20%, var(--gold) 75%);
    -webkit-background-clip: text;
    background-clip: text;
    -webkit-text-fill-color: transparent;
  }
  .ticket-info {
    position: absolute;
    top: 530px; left: 0; width: 100%;
    text-align: center;
    font-family: "Roboto Condensed", sans-serif;
    font-size: 32px;
    line-height: 43px;
    color: var(--white);
  }
  .ticket-info .small { font-size: 21px; }
  .photo-circle {
    position: absolute;
    width: 300px; height: 300px;
    border-radius: 50%;
    border: 9px solid var(--white);
    box-sizing: border-box;
  }
  .photo-santa { left: -60px; top: 588px; background: radial-gradient(circle at 55% 40%, #b03a30, #5a2a1e 60%, #2a1a14); }
  .photo-tree { left: 163px; top: 670px; width: 314px; height: 314px; background: radial-gradient(circle at 58% 50%, #4d8a3a, #7a2a24 45%, #1c1a2a 80%); }
  .photo-skating { left: 458px; top: 670px; width: 314px; height: 314px; background: linear-gradient(180deg, #6a7560, #8e98a6 55%, #b7c2d4); }
  .photo-lights { left: 672px; top: 588px; background: radial-gradient(circle at 45% 45%, #6a3a7a, #2a4a30 55%, #101820); }
  .features {
    position: absolute;
    top: 1002px; left: 0; width: 100%;
    text-align: center;
    font-family: "Roboto", sans-serif;
    font-weight: 500;
    font-size: 20px;
    line-height: 29px;
    color: var(--white);
    text-transform: uppercase;
    margin: 0;
  }
  .location {
    position: absolute;
    top: 1064px; left: 0; width: 100%;
    text-align: center;
    font-family: "Roboto", sans-serif;
    font-size: 19px;
    color: var(--location-gold);
    margin: 0;
  }
  .website {
    position: absolute;
    top: 1094px; left: 0; width: 100%;
    text-align: center;
    font-family: "Roboto", sans-serif;
    font-size: 21px;
    letter-spacing: 5px;
    color: var(--link-blue);
  }
  .partner {
    position: absolute;
    font-family: "Roboto Condensed", sans-serif;
    font-weight: 700;
    text-align: center;
  }
  .partner-harvest {
    left: 28px; top: 1058px; width: 130px;
    font-size: 15px; line-height: 17px;
    color: var(--partner-red);
  }
  .partner-qrm {
    left: 740px; top: 1066px; width: 130px;
    font-size: 30px; line-height: 34px;
    color: var(--partner-navy);
  }
</style>
</head>
<body>
  <main class="flyer">
    <div class="hero-scene" role="img" aria-label="Night photo of a lit-up holiday village street with a glowing blue Ferris wheel and crowds"><div class="hero-shade"></div></div>

    <div class="brand-mark">Frostbell<br>Fairgrounds</div>

    <h1 class="event-title">
      <span class="name">Frostbell Fairgrounds LV</span>
      <span class="tagline">A Magical</span>
      <span class="tagline">Holiday Festival</span>
    </h1>

    <div class="event-dates">Dec 14- Dec 30</div>

    <div class="ticket-info">
      kids 48" and under <strong>FREE</strong>,<br>
      presale tickets $6,<br>
      wonder pass $25<span class="small">(17 days pass)</span>
    </div>

    <div class="photo-circle photo-santa" role="img" aria-label="Santa wrapping gifts in his workshop"></div>
    <div class="photo-circle photo-tree" role="img" aria-label="Giant Christmas tree covered in colourful lights"></div>
    <div class="photo-circle photo-skating" role="img" aria-label="People ice skating in falling snow"></div>
    <div class="photo-circle photo-lights" role="img" aria-label="Trees wrapped in holiday lights with visitors walking"></div>

    <p class="features">Ice skating rink, snow park, santa house, first 1000 kids<br>will receive a gift from Santa on Christmas day.</p>
    <p class="location">Location: Brackenmoor Casino, 4717 Copperfield Lane.</p>
    <div class="website">frostbellfairgroundslv.example</div>

    <div class="partner partner-harvest">Grand Harvest Supper Fair</div>
    <div class="partner partner-qrm">QRM</div>
  </main>
</body>
</html>
```